Business Card Re-Design/Update

We'd like to update out business cards. I've included our current "Style guide" which has the colour scheme of the organisation in it. I've also included the branding files with logos etc in them.

I've also included a copy of one of our existing cards so that you can see how ugly/dated they look. I'd like a fresh modern corporate look.

Target Market(s)

These are for our clients, potential clients, industry contacts - like all business cards

Contact Information for Business Card

Name
Position
Company Address - Level 1, 47 Fernby Street, Carlow Qld 4072
Direct Phone
mobile
Email
Website -www.korvalit.com.au
Logo

Colors

Designer to choose colors to be used in the design.

Requirements
Must have
• Main Logo
• Cards will need to be editable to be able to personalize them for each new employee.
Nice to have
• The MapOut, ShipWell, KeepSteady would be okay to have if they can be sensibly and professionally added to the look without detracting from the main imagery.
• Maybe they could go on the back of the card? will leave this to your creative discretion as to whether/where they fit.
Should not have
• Should not have decorative or script fonts

```html
<!DOCTYPE html>
<html lang="en">
<head>
<meta charset="utf-8">
<title>korvalit — Business Card</title>
<link href="https://fonts.googleapis.com/css2?family=Arimo:wght@400;700&display=swap" rel="stylesheet">
<style>
  :root {
    --stage: #2a2a2c;
    --card-white: #f4f4f4;
    --card-dark: #2b2b2d;
    --brand-red: #d71f26;
    --ink: #555557;
    --ink-soft: #6b6b6d;
    --band-grey: #e2e2e2;
    --on-dark: #e9e9e9;
  }
  * { margin: 0; padding: 0; box-sizing: border-box; }
  html, body { width: 1200px; height: 900px; overflow: hidden; }
  body {
    background: var(--stage);
    font-family: "Arimo", Arial, sans-serif;
    display: flex;
    flex-direction: column;
    align-items: center;
    justify-content: center;
    gap: 56px;
  }
  .card {
    position: relative;
    width: 580px;
    height: 353px;
    box-shadow: 0 14px 30px rgba(0,0,0,.45);
    overflow: hidden;
  }

  /* Front */
  .card--front { background: linear-gradient(160deg, #ffffff 0%, var(--card-white) 100%); }
  .edge-band {
    position: absolute; left: 0; top: 0; bottom: 0; width: 22px;
    background: var(--band-grey);
  }
  .edge-rule {
    position: absolute; left: 22px; top: 0; bottom: 0; width: 3px;
    background: var(--brand-red);
  }
  .brand {
    position: absolute; left: 50px; top: 38px;
    display: flex; align-items: center; gap: 14px;
  }
  .brand__square { width: 34px; height: 34px; background: var(--brand-red); }
  .brand__name {
    font-size: 56px; font-weight: 700; color: var(--ink);
    letter-spacing: -1px; line-height: 1;
  }
  .person { position: absolute; left: 52px; top: 142px; }
  .person__name { font-size: 19px; font-weight: 700; color: var(--brand-red); }
  .person__title { font-size: 13px; color: var(--ink); margin-top: 3px; }
  .contact { position: absolute; left: 52px; top: 206px; list-style: none; }
  .contact__item {
    display: flex; align-items: center; gap: 9px;
    font-size: 12.5px; color: var(--ink); line-height: 21px;
  }
  .contact__icon { width: 13px; height: 13px; fill: var(--brand-red); flex: none; }
  .address {
    position: absolute; right: 40px; bottom: 34px;
    font-size: 12.5px; color: var(--ink-soft); line-height: 18px; text-align: right;
  }

  /* Back */
  .card--back {
    background: linear-gradient(160deg, #333335 0%, var(--card-dark) 60%, #232325 100%);
    display: flex; flex-direction: column; align-items: center; justify-content: center;
  }
  .back-brand { display: flex; align-items: center; gap: 16px; }
  .back-brand .brand__name { color: var(--on-dark); font-size: 64px; }
  .tagline {
    margin-top: 22px; font-size: 14px; color: var(--on-dark); letter-spacing: .5px;
  }
</style>
</head>
<body>

<section class="card card--front" aria-label="Business card front">
  <div class="edge-band"></div>
  <div class="edge-rule"></div>

  <div class="brand">
    <span class="brand__square"></span>
    <span class="brand__name">korvalit</span>
  </div>

  <div class="person">
    <p class="person__name">Dana Whitford</p>
    <p class="person__title">Business Development Manager</p>
  </div>

  <ul class="contact">
    <li class="contact__item">
      <svg class="contact__icon" viewBox="0 0 16 16" aria-hidden="true"><rect x="1" y="5" width="14" height="10" rx="1.5"/><rect x="3" y="1" width="10" height="3" rx="1"/></svg>
      +61 (0) 7 3408 5521
    </li>
    <li class="contact__item">
      <svg class="contact__icon" viewBox="0 0 16 16" aria-hidden="true"><path d="M4 1h3l1 4-2 1.5a9 9 0 0 0 3.5 3.5L11 8l4 1v3a2 2 0 0 1-2 2C7 14 2 9 2 3a2 2 0 0 1 2-2z"/></svg>
      +61 (0) 412 670 394
    </li>
    <li class="contact__item">
      <svg class="contact__icon" viewBox="0 0 16 16" aria-hidden="true"><path d="M1 3h14v10H1z M1 3l7 6 7-6" stroke="#fff" stroke-width="1.2"/></svg>
      dwhitford@korvalit.com.au
    </li>
    <li class="contact__item">
      <svg class="contact__icon" viewBox="0 0 16 16" aria-hidden="true"><circle cx="8" cy="8" r="7"/><path d="M1 8h14M8 1c-3 3-3 11 0 14M8 1c3 3 3 11 0 14" stroke="#fff" stroke-width="1" fill="none"/></svg>
      www.korvalit.com.au
    </li>
  </ul>

  <p class="address">Level 1, 47 Fernby Street,<br>Carlow Qld 4072</p>
</section>

<section class="card card--back" aria-label="Business card back">
  <div class="back-brand brand--inline">
    <span class="brand__square"></span>
    <span class="brand__name">korvalit</span>
  </div>
  <p class="tagline">The MapOut, ShipWell, KeepSteady</p>
</section>

</body>
</html>
```